Tall Fern Roofing Business Card

Need a business card with the logo that was designed here

Contact Information for Business Card

Name, Title, Phone, Email, Website, Company name

```html
<!DOCTYPE html>
<html lang="en">
<head>
<meta charset="UTF-8">
<title>Tall Fern Roofing Business Card</title>
<link href="https://fonts.googleapis.com/css2?family=Poppins:wght@400;600&display=swap" rel="stylesheet">
<style>
  :root {
    --backdrop: #1b1b1b;
    --card-front: #f1f1f1;
    --brand-blue: #1f77c1;
    --edge-grey: #9a9ca0;
    --name-grey: #d3d3d3;
    --white: #ffffff;
    --divider: rgba(255,255,255,0.45);
  }
  * { margin: 0; padding: 0; box-sizing: border-box; }
  html, body {
    width: 1200px; height: 900px; overflow: hidden;
    background: var(--backdrop);
    font-family: "Poppins", sans-serif;
  }
  .stage {
    width: 1200px; height: 900px;
    display: flex; flex-direction: column;
    align-items: center; justify-content: center; gap: 40px;
  }
  .card {
    width: 560px; height: 320px; position: relative; overflow: hidden;
  }
  .card-front {
    background: var(--card-front);
    border-bottom: 10px solid var(--brand-blue);
    display: flex; align-items: center; justify-content: center;
  }
  .brand {
    display: flex; align-items: center; gap: 12px;
    color: var(--brand-blue); font-weight: 600; font-size: 34px;
    letter-spacing: 1px;
  }
  .brand-mark {
    width: 22px; height: 22px; background: var(--brand-blue);
  }
  .card-back {
    background: var(--brand-blue);
    border-bottom: 10px solid var(--edge-grey);
    display: flex; align-items: center;
    padding: 0 40px 30px 50px;
  }
  .person { text-align: right; width: 210px; }
  .person-name {
    color: var(--name-grey); font-weight: 600; font-size: 19px;
    text-transform: uppercase; line-height: 1.2; white-space: nowrap;
  }
  .person-title { color: var(--white); font-size: 14px; margin-top: 2px; }
  .divider {
    width: 1px; height: 80px; background: var(--divider); margin: 0 22px;
  }
  .contact-list { list-style: none; color: var(--white); font-size: 15px; }
  .contact-list li {
    display: flex; align-items: center; gap: 10px; line-height: 1.6;
    white-space: nowrap;
  }
  .contact-list svg { width: 15px; height: 15px; flex: none; }
</style>
</head>
<body>
<main class="stage">
  <section class="card card-front">
    <div class="brand">
      <span class="brand-mark"></span>
      <span class="brand-name">Tall Fern Roofing</span>
    </div>
  </section>

  <section class="card card-back">
    <div class="person">
      <p class="person-name">Marcus Hale</p>
      <p class="person-title">Managing Director</p>
    </div>
    <div class="divider"></div>
    <ul class="contact-list">
      <li>
        <svg viewBox="0 0 24 24" fill="none" stroke="#fff" stroke-width="2"><path d="M5 3h4l2 5-3 2a11 11 0 0 0 6 6l2-3 5 2v4a2 2 0 0 1-2 2A17 17 0 0 1 3 5a2 2 0 0 1 2-2z"/></svg>
        <span>021-987 654 320</span>
      </li>
      <li>
        <svg viewBox="0 0 24 24" fill="none" stroke="#fff" stroke-width="2"><rect x="2" y="5" width="20" height="14"/><path d="M2 5l10 8 10-8"/></svg>
        <span>mail@tallfern.co</span>
      </li>
      <li>
        <svg viewBox="0 0 24 24" fill="none" stroke="#fff" stroke-width="2"><circle cx="12" cy="12" r="10"/><path d="M2 12h20M12 2c3 3 3 17 0 20M12 2c-3 3-3 17 0 20"/></svg>
        <span>www.tallfern.co</span>
      </li>
    </ul>
  </section>
</main>
</body>
</html>
```